IV Nutritional Clinic Web Design

We are working with Velqo. They are an IV Nutritional Clinic and in need of a new website design.
Some sites to use for inspiration:
https://brightpathcareco.com
https://www.ourzavrowellness.com
https://www.dewspringlounge.com
https://qvitalsurge.com
https://www.lumo-vital.com/pages/iv-therapy-west-hollywood
https://www.tqoncologyhub.com/cancer-care/iv-drips/
https://dripwellary.com
https://corvinahealthhub.com
Thank you for taking the time to consider designing a website for us. We are web developers based in Stockton, CA, USA. Most of our projects go through the same process. Understanding this process may help you win a project with us. We custom-code all of our websites in-house. We don’t have any requirements as to what tools you use for your design, but we prefer Figma files. For any design that we label as four-stars, we send it to the client for review. The client picks the final design they want us to use. Once we complete this process, we will continue to show additional clients all the four-star sites and purchase them later. Your designs will have multiple chances to sell. For better chances of success, we ask that you follow these guidelines.
IMAGES:
If you use any images or icons in the design, we ask that you have a link to the asset so we can purchase the image/icon. Most of the designs we submit do not have the customer’s images on them unless they have some great images. Be creative; show us the feeling you are trying to portray with your image choices. Use any royalty-free site you choose. We subscribe to Pixvane and mainly use their images, but we can purchase images outside of Pixvane.
PLEASE NOTE: we will not submit designs to clients with watermarks on the images.
FONTS:
We ask that you identify the fonts used in the design. This can be done in a message if you want. We typically use Revuo Fonts and Pixvane Fonts.
CONTENT:
We're always open to different content and ideas. We often submit designs with stock images so the client can see our vision. We typically take pictures after the website launch to use their images with our vision. Lorem Ipsum is fine for paragraphs, but we ask that you write the headers in correct English. We want to be able to show the vision and identify the sections of the website.
INSPIRATION:
We typically add a couple of links in the brief of websites we like to help you get started in your design.
REVISIONS:
We do not often ask for revisions of the designs unless we see something in the design that may not appeal to the client. If there are slight changes that we want to make, we do that in the development process.
FEEDBACK:
We rarely give feedback on designs during the design process. We are working on many website projects and do not have the time to provide feedback. We usually respond if your request is well thought out and asks specific questions, but a note asking “feedback, please” usually goes unanswered.

```html
<!DOCTYPE html>
<html lang="en">
<head>
<meta charset="utf-8">
<title>Velqo Hydration – IV Therapy</title>
<link href="https://fonts.googleapis.com/css2?family=Lexend:wght@400;500;600&family=Roboto:wght@400;500;700;900&display=swap" rel="stylesheet">
<style>
:root{
  --navy:#16166b;
  --green:#6b9a33;
  --green-soft:#7aa844;
  --ink:#1d1d1d;
  --muted:#555;
  --line:#d9d9d9;
  --footer:#2d2d2d;
  --white:#fff;
}
*{box-sizing:border-box;margin:0;padding:0}
html,body{width:1200px;height:4894px;overflow:hidden}
body{position:relative;background:var(--white);font-family:"Roboto",sans-serif;color:var(--ink)}
.section{position:absolute;left:0;width:1200px}
.abs{position:absolute}
.btn{position:absolute;display:flex;align-items:center;justify-content:center;background:var(--navy);color:var(--white);font:700 15px "Roboto",sans-serif;letter-spacing:.3px;border-radius:3px}
.h2{font:500 38px "Lexend",sans-serif;color:var(--ink)}
.h2 em{font-style:normal;color:var(--green)}
.rule{position:absolute;height:3px;background:var(--green)}

/* top bar */
.topbar{top:0;height:59px;background:var(--navy)}
.topbar .contact{position:absolute;top:0;height:59px;display:flex;align-items:center;gap:10px;color:var(--white);font-size:14px}
.topbar .dot{width:30px;height:30px;border-radius:50%;background:var(--white);display:flex;align-items:center;justify-content:center}
.topbar .book{left:956px;top:11px;width:131px;height:38px;background:var(--green);font-size:15px}

/* header */
.header{top:59px;height:103px;background:var(--white)}
.brand{position:absolute;left:108px;top:20px;font:600 48px "Lexend",sans-serif;color:var(--navy);letter-spacing:2px}
.nav a{position:absolute;top:40px;font-size:15px;color:var(--ink);text-decoration:none}
.nav a.active{color:var(--navy);border-bottom:2px solid var(--navy);padding-bottom:2px}

/* hero */
.hero{top:162px;height:618px;overflow:hidden}
.hero-photo{position:absolute;inset:0;background:linear-gradient(90deg,#d9d4cd 0%,#ecebe8 35%,#e6e6e4 70%,#d5d6d5 100%)}
.hero-title{position:absolute;left:560px;width:556px;top:166px;text-align:center;font:700 42px/48px "Roboto",sans-serif;color:#111}
.hero-title em{font-style:normal;color:var(--navy)}
.hero-text{position:absolute;left:560px;width:556px;top:274px;text-align:center;font-size:16px;line-height:29px;color:#222}
.hero .btn{left:752px;top:351px;width:173px;height:36px;font-size:15px}
.hero-wave{position:absolute;left:0;top:480px}

/* about */
.about{top:780px;height:600px}
.about p{position:absolute;left:108px;top:160px;width:490px;font-size:13.5px;line-height:28.5px;color:#333}
.about .frame{position:absolute;left:720px;top:50px;width:386px;height:340px;border:2px solid #444}
.about .photo{position:absolute;left:703px;top:67px;width:386px;height:353px;background:linear-gradient(135deg,#f1f1f1,#d8d8d6 60%,#bdbcb8)}

/* services */
.services{top:1260px;height:1320px}
.card{position:absolute;width:298px;height:422px;border:1.5px solid #e3e3e3;background:var(--white);text-align:center}
.card.raised{box-shadow:0 6px 18px rgba(0,0,0,.14)}
.card .pic{position:absolute;left:18px;top:18px;width:262px;height:237px}
.card h3{position:absolute;left:0;right:0;top:276px;font:500 20px "Roboto",sans-serif;letter-spacing:.3px;color:#1a1a1a}
.card p{position:absolute;left:26px;right:26px;top:308px;font-size:13.5px;line-height:20px;color:#444}
.card .more{position:absolute;left:0;right:0;top:384px;display:flex;justify-content:center;align-items:center;gap:10px;font:700 13.5px "Roboto",sans-serif;color:var(--navy)}

/* why */
.why{top:2597px;height:541px;background:linear-gradient(180deg,#6c9b36,#6a9a33);color:var(--white)}
.why .h2{color:var(--white)}
.why-card{position:absolute;top:216px;width:302px;height:246px;border-radius:34px;background:var(--white);text-align:center;color:var(--ink)}
.why-card .ico{position:absolute;left:103px;top:20px;width:96px;height:96px;border-radius:50%;display:flex;align-items:center;justify-content:center}
.why-card .ico.g{background:var(--green);box-shadow:0 0 0 5px #e8efde}
.why-card .ico.n{background:var(--navy);box-shadow:0 0 0 5px #e2e2ef}
.why-card h3{position:absolute;left:0;right:0;top:133px;font:500 18px "Roboto",sans-serif}
.why-card p{position:absolute;left:0;right:0;top:170px;font-size:13.5px;color:#444}
.why-card .link{position:absolute;left:0;right:0;top:202px;display:flex;justify-content:center;gap:10px;align-items:center;font-size:15px}
.link.g{color:var(--green)} .link.n{color:var(--navy)}

/* reviews */
.reviews{top:3138px;height:620px}
.review{position:absolute;top:168px;width:302px;height:306px;background:var(--white);box-shadow:0 3px 14px rgba(0,0,0,.13)}
.review .q{position:absolute;left:16px;top:8px;font:900 44px "Roboto",sans-serif;color:var(--green)}
.review .q.end{left:auto;right:14px;top:248px;color:#cfd6c4}
.review.mid .q:not(.end){color:var(--navy)}
.review p{position:absolute;left:18px;right:18px;top:56px;font-size:12.5px;line-height:23.5px;color:#444}
.review .stars{position:absolute;left:18px;top:172px;font-size:20px;letter-spacing:4px;color:var(--green)}
.review.mid .stars{color:var(--navy)}
.review .who{position:absolute;left:18px;top:208px;font:700 13.5px "Roboto",sans-serif;color:var(--green)}
.review.mid .who{color:var(--navy)}
.review .tag{position:absolute;left:18px;top:233px;font-size:11.5px;color:#222}
.review .src{position:absolute;left:18px;top:264px;font:500 17px "Roboto",sans-serif;color:#555}

/* contact */
.contact{top:3758px;height:745px}
.field{position:absolute;height:44px;border:1.5px solid #cfcfcf;border-radius:3px;font-size:12px;color:#777;padding-left:14px;display:flex;align-items:center}
.contact .mark{position:absolute;left:661px;top:330px;width:426px;text-align:center;font:600 104px "Lexend",sans-serif;color:var(--navy);letter-spacing:6px}

/* footer */
.footer{top:4440px;height:454px}
.footer-band{position:absolute;left:0;top:60px;width:1200px;height:394px;background:var(--footer)}
.footer .mark{position:absolute;left:0;right:0;top:128px;text-align:center;font:600 62px "Lexend",sans-serif;color:var(--white);letter-spacing:4px}
.footer-links{position:absolute;left:0;right:0;top:270px;display:flex;justify-content:center;gap:28px;color:var(--white);font-size:15.5px}
.footer-links span.sep{color:#ccc}
.socials{position:absolute;left:0;right:0;top:322px;display:flex;justify-content:center;gap:8px}
.socials span{width:34px;height:34px;border-radius:50%;border:2px solid var(--white)}
.footer .line{position:absolute;left:110px;width:978px;top:390px;height:1px;background:#8a8a8a}
.footer .copy{position:absolute;left:0;right:0;top:416px;text-align:center;color:var(--white);font-size:15px}
</style>
</head>
<body>

<div class="section topbar">
  <div class="contact" style="left:110px">
    <span class="dot"><svg width="16" height="16" viewBox="0 0 24 24"><path fill="#16166b" d="M6.6 10.8a15 15 0 0 0 6.6 6.6l2.2-2.2c.3-.3.7-.4 1-.2 1.1.4 2.3.6 3.6.6.6 0 1 .4 1 1V20c0 .6-.4 1-1 1A17 17 0 0 1 3 4c0-.6.4-1 1-1h3.5c.6 0 1 .4 1 1 0 1.3.2 2.5.6 3.6.1.3 0 .7-.2 1z"/></svg></span>
    +1 555 010 2040
  </div>
  <div class="contact" style="left:294px">
    <span class="dot"><svg width="16" height="16" viewBox="0 0 24 24"><path fill="#16166b" d="M3 5h18v14H3z"/><path fill="none" stroke="#fff" stroke-width="2" d="M3 6l9 7 9-7"/></svg></span>
    hello@velqomail.com
  </div>
  <div class="btn book">BOOK NOW</div>
</div>

<header class="section header">
  <div class="brand">VELQO</div>
  <nav class="nav">
    <a class="active" style="left:391px">Home</a>
    <a style="left:471px">About Us</a>
    <a style="left:572px">IV Therapy&nbsp;&nbsp;⌄</a>
    <a style="left:707px">Membership &amp; Pricing</a>
    <a style="left:895px">FAQ</a>
    <a style="left:961px">Contact &amp; Booking</a>
  </nav>
</header>

<section class="section hero">
  <div class="hero-photo" role="img" aria-label="Woman in a white robe relaxing in a lounge chair during an IV drip, holding a drink"></div>
  <h1 class="hero-title">REHYDRATE. <em>REVITALIZE.</em><br>REPLENISH.</h1>
  <p class="hero-text">Feel your best with IV therapy—fast hydration, essential nutrients, and instant energy. Book your drip today!</p>
  <div class="btn">BOOK YOUR DRIP</div>
  <svg class="hero-wave" width="1200" height="140" viewBox="0 0 1200 140">
    <path d="M0 80 C200 150 420 130 640 90 S1000 20 1200 40 L1200 140 L0 140 Z" fill="#fff"/>
    <path d="M0 80 C200 150 420 130 640 90 S1000 20 1200 40" fill="none" stroke="#6b9a33" stroke-width="14"/>
  </svg>
</section>

<section class="section about">
  <h2 class="h2 abs" style="left:108px;top:80px">About <em>Us</em></h2>
  <div class="rule" style="left:108px;top:140px;width:86px"></div>
  <p>At Velqo, we believe that true wellness starts from within. Our mission is to help you hydrate, restore, and revitalize through expertly crafted IV therapy treatments tailored to your needs. Whether you’re looking to boost energy, enhance immunity, accelerate recovery, or achieve radiant skin, our science-backed infusions deliver essential nutrients directly to your body—fast and effectively.</p>
  <div class="btn" style="left:108px;top:343px;width:175px;height:38px">LEARN MORE</div>
  <div class="frame"></div>
  <div class="photo" role="img" aria-label="Couple in white robes relaxing in lounge chairs during IV therapy"></div>
</section>

<section class="section services">
  <svg class="abs" style="left:0;top:0" width="1200" height="110" viewBox="0 0 1200 110">
    <path d="M10 60 C200 10 420 15 640 60 S1000 120 1190 65" fill="none" stroke="#6b9a33" stroke-width="8"/>
  </svg>
  <h2 class="h2 abs" style="left:0;right:0;top:100px;text-align:center">IV <em>Therapy</em> Services</h2>
  <div class="rule" style="left:514px;top:160px;width:110px"></div>
  <p class="abs" style="left:0;right:0;top:185px;text-align:center;font-size:16.5px;line-height:30px;color:#444">Customized IV Therapy for Hydration, Energy, Immunity, and Wellness—Designed to<br>Help You Feel Your Best.</p>

  <div class="card" style="left:108px;top:305px">
    <div class="pic" role="img" aria-label="Man in a jacket stretching outdoors before exercise" style="background:linear-gradient(160deg,#5c7a4a,#2a3350 55%,#6d8a5c)"></div>
    <h3>Energy &amp; Performance</h3>
    <p>Boost stamina, fight fatigue, and power through your day with our energizing IV drip.</p>
    <div class="more">BOOK NOW <svg width="12" height="12" viewBox="0 0 12 12"><rect x="1" y="2" width="10" height="9" fill="none" stroke="#16166b" stroke-width="1.5"/><path d="M1 5h10M4 1v2M8 1v2" stroke="#16166b" stroke-width="1.5"/></svg></div>
  </div>
  <div class="card raised" style="left:452px;top:305px">
    <div class="pic" role="img" aria-label="Man seated in a treatment chair receiving an IV drip" style="background:linear-gradient(160deg,#efe9df,#c9b9a1 60%,#e7e2da)"></div>
    <h3>Immune Boost</h3>
    <p>Strengthen your immune system and protect your body with essential vitamins and antioxidants.</p>
    <div class="more" style="color:var(--green)">BOOK NOW <svg width="12" height="12" viewBox="0 0 12 12"><rect x="1" y="2" width="10" height="9" fill="none" stroke="#6b9a33" stroke-width="1.5"/><path d="M1 5h10M4 1v2M8 1v2" stroke="#6b9a33" stroke-width="1.5"/></svg></div>
  </div>
  <div class="card" style="left:792px;top:305px">
    <div class="pic" role="img" aria-label="Glowing blue illustration of a human liver" style="background:radial-gradient(circle at 50% 50%,#dbe9f7,#5f8fc6 60%,#2b5a98)"></div>
    <h3>Detox &amp; Recovery</h3>
    <p>Flush out toxins, speed up recovery, and feel refreshed from the inside out.</p>
    <div class="more">BOOK NOW <svg width="12" height="12" viewBox="0 0 12 12"><rect x="1" y="2" width="10" height="9" fill="none" stroke="#16166b" stroke-width="1.5"/><path d="M1 5h10M4 1v2M8 1v2" stroke="#16166b" stroke-width="1.5"/></svg></div>
  </div>

  <div class="card" style="left:108px;top:753px">
    <div class="pic" role="img" aria-label="Woman with glowing skin and closed eyes touching her cheek" style="background:linear-gradient(150deg,#f4efe8,#d9c2a8 55%,#efe6dc)"></div>
    <h3>Beauty &amp; Anti-Aging</h3>
    <p>Glow from within—hydrate, nourish, and rejuvenate your skin for a radiant, youthful look.</p>
    <div class="more">BOOK NOW <svg width="12" height="12" viewBox="0 0 12 12"><rect x="1" y="2" width="10" height="9" fill="none" stroke="#16166b" stroke-width="1.5"/><path d="M1 5h10M4 1v2M8 1v2" stroke="#16166b" stroke-width="1.5"/></svg></div>
  </div>
  <div class="card" style="left:452px;top:753px">
    <div class="pic" role="img" aria-label="Nutritionist consulting a patient across a desk with fresh fruit" style="background:linear-gradient(160deg,#eef0ee,#c9cfd4 55%,#b99a6e)"></div>
    <h3>Signature Cocktail</h3>
    <p>The ultimate wellness infusion—restore balance, fight stress, and revitalize your body.</p>
    <div class="more">BOOK NOW <svg width="12" height="12" viewBox="0 0 12 12"><rect x="1" y="2" width="10" height="9" fill="none" stroke="#16166b" stroke-width="1.5"/><path d="M1 5h10M4 1v2M8 1v2" stroke="#16166b" stroke-width="1.5"/></svg></div>
  </div>
  <div class="card" style="left:792px;top:753px">
    <div class="pic" role="img" aria-label="IV bag hanging on a metal drip stand" style="background:linear-gradient(160deg,#b8a27c,#8d8f86 50%,#c9c2ad)"></div>
    <h3>Custom Drips</h3>
    <p>Personalized IV therapy tailored to your unique wellness goals and lifestyle.</p>
    <div class="more">BOOK NOW <svg width="12" height="12" viewBox="0 0 12 12"><rect x="1" y="2" width="10" height="9" fill="none" stroke="#16166b" stroke-width="1.5"/><path d="M1 5h10M4 1v2M8 1v2" stroke="#16166b" stroke-width="1.5"/></svg></div>
  </div>

  <div class="btn" style="left:513px;top:1219px;width:175px;height:40px">BOOK NOW</div>
</section>

<section class="section why">
  <h2 class="h2 abs" style="left:0;right:0;top:68px;text-align:center">Why Choose Velqo?</h2>
  <div class="rule" style="left:546px;top:132px;width:108px;background:#fff"></div>
  <p class="abs" style="left:0;right:0;top:155px;text-align:center;font-size:17px;font-weight:500">Experience the Velqo difference. Feel better, perform better, live better.</p>

  <div class="why-card" style="left:114px">
    <div class="ico g"><svg width="40" height="44" viewBox="0 0 40 44"><rect x="8" y="8" width="16" height="26" rx="3" fill="none" stroke="#fff" stroke-width="3"/><path d="M12 18h8M12 24h8M16 34v8M30 6v22" stroke="#fff" stroke-width="3"/></svg></div>
    <h3>Medical-Grade IV Therapies</h3>
    <p>Administered by trained professionals</p>
    <div class="link g">Learn More <svg width="18" height="12" viewBox="0 0 18 12"><path d="M0 6h15M11 1l5 5-5 5" fill="none" stroke="#6b9a33" stroke-width="2"/></svg></div>
  </div>
  <div class="why-card" style="left:450px">
    <div class="ico n"><svg width="40" height="44" viewBox="0 0 40 44"><rect x="8" y="10" width="24" height="30" rx="4" fill="none" stroke="#fff" stroke-width="3"/><path d="M14 4h12v6H14zM13 26l5 5 9-10" fill="none" stroke="#fff" stroke-width="3"/></svg></div>
    <h3>Fast &amp; Effective Hydration</h3>
    <p>Feel the benefits immediately</p>
    <div class="link n">Learn More <svg width="18" height="12" viewBox="0 0 18 12"><path d="M0 6h15M11 1l5 5-5 5" fill="none" stroke="#16166b" stroke-width="2"/></svg></div>
  </div>
  <div class="why-card" style="left:786px">
    <div class="ico g"><svg width="44" height="40" viewBox="0 0 44 40"><rect x="4" y="6" width="36" height="30" rx="4" fill="none" stroke="#fff" stroke-width="3"/><path d="M4 14h36M13 2v8M31 2v8M15 24l5 5 9-9" fill="none" stroke="#fff" stroke-width="3"/></svg></div>
    <h3>Tailored to Your Needs</h3>
    <p>Custom blends for wellness, energy.</p>
    <div class="link g">Learn More <svg width="18" height="12" viewBox="0 0 18 12"><path d="M0 6h15M11 1l5 5-5 5" fill="none" stroke="#6b9a33" stroke-width="2"/></svg></div>
  </div>
</section>

<section class="section reviews">
  <h2 class="h2 abs" style="left:0;right:0;top:58px;text-align:center">User <em>Reviews</em></h2>
  <div class="rule" style="left:544px;top:120px;width:112px"></div>

  <div class="review" style="left:112px">
    <div class="q">“</div>
    <p>I was feeling constantly drained, but after my first IV drip at Velqo, I felt an immediate boost! The process was smooth, and the staff was incredibly professional. Now, I make it a part of my routine!</p>
    <div class="stars">☆☆☆☆☆</div>
    <div class="who">— Dana R.</div>
    <div class="tag">Game Changer for My Energy Levels!</div>
    <div class="src">Revuo</div>
    <div class="q end">”</div>
  </div>
  <div class="review mid" style="left:448px">
    <div class="q">“</div>
    <p>As an athlete, recovery is everything. The performance IV therapy at Velqo helps me bounce back quicker and stay at my best. Highly recommend!</p>
    <div class="stars">★★★★★</div>
    <div class="who">— Owen K.</div>
    <div class="tag">Fast Recovery After Workouts!</div>
    <div class="src">Revuo</div>
    <div class="q end">”</div>
  </div>
  <div class="review" style="left:785px">
    <div class="q">“</div>
    <p>I tried the Beauty &amp; Anti-Aging drip, and WOW—my skin is glowing! I feel more hydrated, refreshed, and energized. This is now my go-to self-care treatment!</p>
    <div class="stars">☆☆☆☆☆</div>
    <div class="who">— Leah P.</div>
    <div class="tag">My Skin Has Never Looked Better!</div>
    <div class="src">Revuo</div>
    <div class="q end">”</div>
  </div>

  <div class="btn" style="left:492px;top:519px;width:217px;height:40px">VIEW ALL REVIEWS</div>
</section>

<section class="section contact">
  <svg class="abs" style="left:0;top:0" width="1200" height="110" viewBox="0 0 1200 110">
    <path d="M0 70 C200 110 420 80 640 40 S1000 0 1190 50" fill="none" stroke="#6b9a33" stroke-width="10"/>
  </svg>
  <h2 class="h2 abs" style="left:100px;top:168px">Contact <em>Us</em></h2>
  <div class="field" style="left:100px;top:266px;width:223px">First Name</div>
  <div class="field" style="left:370px;top:266px;width:219px">Last Name</div>
  <div class="field" style="left:100px;top:329px;width:489px">Phone Number</div>
  <div class="field" style="left:100px;top:390px;width:489px">Email Address</div>
  <div class="field" style="left:100px;top:451px;width:489px;justify-content:space-between;padding-right:22px">Type of Service <span style="color:#333;font-size:10px">▼</span></div>
  <div class="btn" style="left:100px;top:530px;width:217px;height:38px">SUBMIT NOW</div>
  <div class="mark">VELQO</div>
</section>

<footer class="section footer">
  <div class="footer-band"></div>
  <svg class="abs" style="left:0;top:0" width="1200" height="130" viewBox="0 0 1200 130">
    <path d="M0 70 C200 10 420 30 640 60 S1000 110 1200 50 L1200 130 L0 130 Z" fill="#2d2d2d"/>
    <path d="M0 70 C200 10 420 30 640 60 S1000 110 1200 50" fill="none" stroke="#6b9a33" stroke-width="12"/>
  </svg>
  <div class="mark">VELQO</div>
  <div class="footer-links">
    <span>Home</span><span class="sep">|</span><span>About Us</span><span class="sep">|</span><span>IV Therapy</span><span class="sep">|</span><span>Membership &amp; Pricing</span><span class="sep">|</span><span>FAQ</span><span class="sep">|</span><span>Contact &amp; Booking</span>
  </div>
  <div class="socials"><span></span><span></span><span></span><span></span><span></span></div>
  <div class="line"></div>
  <div class="copy">© 2025 Velqo. All Rights Reserved.</div>
</footer>

</body>
</html>
```